Halvery Construction Group Website

Need a dynamic corporate website that can be built on with time. We want to get our information out to the world and have a place where customers can submit requests for proposals.

Target Market(s)

Custom home owners and buyers. Architects and Real Estate Agents.

Industry/Entity Type

Construction

Number of Pages Required

3 page

Font styles to use
Serif
Sans Serif

Requirements
Must have
• Company logo, about, company contact information, biography, contact, projects,
• Sleek, modern, clean, attractive design.
• Online form customers can use for filling out a request for project proposal.
• Linkedin hyperlink.
• Uses www.halveryconstructiongroup.example

```html
<!DOCTYPE html>
<html lang="en">
<head>
<meta charset="utf-8">
<title>Halvery Construction Group</title>
<link rel="stylesheet" href="https://fonts.googleapis.com/css2?family=Michroma&family=Roboto:wght@300;400;500;700&display=swap">
<style>
:root{
  --navy:#0c2a5a;
  --brand:#1a4a9c;
  --brand-dark:#0e3f8c;
  --accent:#2c7fd0;
  --ink:#1d2a44;
  --paper:#f7f8f6;
  --white:#ffffff;
  --line:#c7ccd6;
}
*{box-sizing:border-box;margin:0;padding:0}
html,body{width:1120px;height:1200px;overflow:hidden}
body{font-family:'Roboto',sans-serif;color:var(--ink);background:var(--white);position:relative}

.hero{position:absolute;left:0;top:0;width:1120px;height:497px;
  background:linear-gradient(160deg,#1b2b4e 0%,#2a3a5c 35%,#1e3a6a 60%,#3b5f8c 100%);color:var(--white)}
.hero__photo{position:absolute;inset:0;background:
  radial-gradient(ellipse at 75% 30%,rgba(120,160,210,.35),transparent 60%),
  radial-gradient(ellipse at 20% 70%,rgba(90,80,70,.35),transparent 55%)}
.brand{position:absolute;left:92px;top:34px;display:flex;align-items:center;gap:12px}
.brand__square{width:56px;height:56px;background:var(--white);border-radius:6px}
.brand__name{font-family:'Roboto',sans-serif;font-weight:700;font-size:34px;letter-spacing:2px;color:var(--white)}
.nav{position:absolute;top:46px;left:602px;display:flex}
.nav a{color:var(--white);text-decoration:none;font-size:15px;font-weight:500;height:35px;line-height:35px;padding:0 12px;margin-right:12px}
.nav a.is-active{background:var(--accent);border:1px solid #cfe0f5;border-radius:2px}
.hero__title{position:absolute;top:244px;left:0;width:1120px;text-align:center;font-family:'Michroma',sans-serif;font-size:38px;letter-spacing:1px}
.hero__sub{position:absolute;top:314px;left:0;width:1120px;text-align:center;font-size:24px;font-weight:300}
.hero__arrow{position:absolute;top:282px}
.hero__arrow--prev{left:25px}
.hero__arrow--next{left:1062px}
.hero__rule{position:absolute;left:0;top:497px;width:1120px;height:4px;background:var(--accent)}

.info{position:absolute;left:0;top:501px;width:1120px;height:309px}
.info__map{position:absolute;inset:0;background:linear-gradient(90deg,#eef1ea 0%,#f6f6f2 50%,#e7eef2 100%)}
.info__logo{position:absolute;left:92px;top:92px;width:220px;text-align:center}
.info__logo-square{width:56px;height:56px;background:var(--brand);margin:0 auto 14px;border-radius:6px}
.info__logo-name{font-weight:700;font-size:30px;letter-spacing:2px;color:var(--brand)}
.col{position:absolute;top:40px}
.col h2{font-size:18px;font-weight:700;color:var(--brand);letter-spacing:.3px}
.col h2::after{content:"";display:block;width:97px;height:2px;background:var(--brand);margin-top:11px}
.quick{left:359px}
.quick ul{list-style:none;margin-top:20px}
.quick li{font-size:14px;height:29.5px;color:var(--ink)}
.quick li::before{content:"›";margin-right:6px}

.contact{left:511px;width:230px;height:260px}
.contact__icon{position:absolute;left:0;width:36px;height:36px;border:2px solid var(--brand);border-radius:50%;display:flex;align-items:center;justify-content:center}
.contact__text{position:absolute;left:52px;width:180px;font-size:12px;line-height:19px;color:var(--ink)}
.contact__name{display:block;font-size:12.5px;font-weight:500;white-space:nowrap}
.contact__label{display:block;font-size:15px;font-weight:500;line-height:22px}
.contact__value{font-weight:500}

.form{left:759px;width:268px}
.form__field{position:absolute;border:1px solid var(--line);border-radius:3px;background:var(--white);font-size:11px;padding:10px 10px;color:#333}
.form__btn{position:absolute;left:0;top:134px;width:111px;height:36px;background:var(--brand-dark);color:var(--white);font-size:13px;font-weight:700;line-height:36px;text-align:center;border-radius:2px}

.bar{position:absolute;left:0;top:810px;width:1120px;height:57px;background:var(--brand-dark);color:var(--white)}
.bar__copy{position:absolute;left:91px;top:19px;font-size:13.5px}
.bar__social{position:absolute;left:885px;top:13px;display:flex;gap:6px}
.bar__social span{width:31px;height:31px;border:2px solid var(--white);border-radius:50%}

.feature{position:absolute;top:867px;width:560px;height:333px;color:var(--white);text-align:center}
.feature--projects{left:0;background:linear-gradient(135deg,#4a8ed0,#3f86cc 50%,#5ea0dc)}
.feature--news{left:560px;background:linear-gradient(135deg,#2d63b8,#3a73c4 50%,#2a5cb2)}
.feature__label{font-size:20px;font-weight:400}
.feature--projects .feature__label{margin-top:124px}
.feature--projects .feature__title{font-size:34px;font-weight:700;margin-top:14px}
.feature--news .feature__label{margin-top:115px}
.feature--news .feature__title{font-size:20px;font-weight:500;line-height:32px;margin-top:14px}
</style>
</head>
<body>

<header class="hero">
  <div class="hero__photo" role="img" aria-label="Night view looking up at a steel-frame building under construction with a crane and glass towers"></div>
  <div class="brand"><span class="brand__square"></span><span class="brand__name">HALVERY</span></div>
  <nav class="nav">
    <a class="is-active" href="#">HOME</a><a href="#">ABOUT</a><a href="#">BIO</a><a href="#">PROJECTS</a><a href="#">CONTACT US</a>
  </nav>
  <h1 class="hero__title">HALVERY CONSTRUCTION GROUP</h1>
  <p class="hero__sub">Commercial, Residential and Community Solutions</p>
  <svg class="hero__arrow hero__arrow--prev" width="30" height="52" viewBox="0 0 30 52"><polyline points="27,2 3,26 27,50" fill="none" stroke="#fff" stroke-width="2"/></svg>
  <svg class="hero__arrow hero__arrow--next" width="30" height="52" viewBox="0 0 30 52"><polyline points="3,2 27,26 3,50" fill="none" stroke="#fff" stroke-width="2"/></svg>
</header>
<div class="hero__rule"></div>

<section class="info">
  <div class="info__map" role="img" aria-label="Faded map of Australia behind the footer content"></div>
  <div class="info__logo"><div class="info__logo-square"></div><div class="info__logo-name">HALVERY</div></div>

  <div class="col quick">
    <h2>QUICK LINKS</h2>
    <ul><li>Home</li><li>About</li><li>Bio</li><li>Projects</li><li>Contact Us</li></ul>
  </div>

  <div class="col contact">
    <h2>CONTACT US</h2>

    <span class="contact__icon" style="top:59px"><svg width="12" height="14" viewBox="0 0 12 14"><path d="M6 1a4 4 0 0 0-4 4c0 3 4 8 4 8s4-5 4-8a4 4 0 0 0-4-4z" fill="none" stroke="#1a4a9c" stroke-width="1.6"/><circle cx="6" cy="5" r="1.3" fill="#1a4a9c"/></svg></span>
    <div class="contact__text" style="top:59px"><span class="contact__name">HALVERY CONSTRUCTION,</span>Larkfield Vale, Western<br>Australia, 6099.</div>

    <span class="contact__icon" style="top:131px"><svg width="10" height="14" viewBox="0 0 10 14"><rect x="1" y="1" width="8" height="12" rx="1.5" fill="none" stroke="#1a4a9c" stroke-width="1.6"/><line x1="4" y1="11" x2="6" y2="11" stroke="#1a4a9c" stroke-width="1.4"/></svg></span>
    <div class="contact__text" style="top:129px"><span class="contact__label">PHONE:</span><span class="contact__value">1800 4410 7752</span></div>

    <span class="contact__icon" style="top:188px"><svg width="13" height="10" viewBox="0 0 13 10"><rect x="0" y="0" width="13" height="10" rx="1.5" fill="#1a4a9c"/><polyline points="1,1.5 6.5,6 12,1.5" fill="none" stroke="#fff" stroke-width="1.2"/></svg></span>
    <div class="contact__text" style="top:185px"><span class="contact__label">Mail:</span><span class="contact__value">info@halveryconstruction<br>group.example</span></div>
  </div>

  <div class="col form">
    <h2>CONTACT FORM</h2>
    <div style="position:relative">
      <div class="form__field" style="left:1px;top:20px;width:128px;height:32px">Name</div>
      <div class="form__field" style="left:139px;top:20px;width:128px;height:32px">Phone</div>
      <div class="form__field" style="left:1px;top:60px;width:266px;height:60px">Message</div>
      <div class="form__btn">SEND MESSAGE</div>
    </div>
  </div>
</section>

<footer class="bar">
  <p class="bar__copy">Copyright © 2016 Halvery Construction Group. All Right Reserved</p>
  <div class="bar__social" aria-label="Social links"><span></span><span></span><span></span><span></span></div>
</footer>

<section class="feature feature--projects" role="img" aria-label="Blue-tinted photo of hands stacking wooden blocks">
  <p class="feature__label">Featured Community Projects Item</p>
  <p class="feature__title">Halvery Construction Group</p>
</section>
<section class="feature feature--news" role="img" aria-label="Blue-tinted photo of people reviewing plans at a desk">
  <p class="feature__label">Featured News Item</p>
  <p class="feature__title">Nemo enim ipsam voluptatem quia voluptas<br>sit aspernatur aut odit aut fugit</p>
</section>

</body>
</html>
```